Brightgate Audio Video Security LLC

Need help designing a web page for an alarm company. I want to promote my business.

Target Market(s)

Residential and commercial clients

Industry/Entity Type

Security Service

Coding

Coded - Design and coding required

Number of Pages Required

2 page

Font styles to use
Sans Serif

Requirements
Must have
• I would llike my logo displayed on the page. I would like my slogan displayed as well
´´A GREAT PLACE FOR YOUR SECURITY NEEDS´´
We are licensed and insured
Company phone number 832-555-0147
Company hours: Monday-Friday 8am-5pm Company address: P.O. Box 419 Larkfield, TX 77519 over 25 years experience
Email info. Brightgatesys@kelvamail.com
Company license #K41862509
Fire license# MTQ-6071852
LUV-8146027
We offer alarm monitoring,security cameras, access control,gate openers, home theater systems, covert camera installations, FIre alarm installation and monitoring
Nice to have
• We offer security at competitive prices.
Get customer information for a free quote similar to qmr website.
Should not have
• No prices listed on website

```html
<!DOCTYPE html>
<html lang="en">
<head>
<meta charset="utf-8">
<title>Brightgate Audio Video Security LLC</title>
<link rel="stylesheet" href="https://fonts.googleapis.com/css2?family=Playfair+Display:wght@400;700&family=Raleway:ital,wght@0,400;0,500;0,600;0,700;1,400;1,500&display=swap">
<style>
:root{
  --red:#e8202a;
  --ink:#2a2a2a;
  --muted:#8a8a8a;
  --line:#cfcfcf;
  --soft:#f5f5f6;
  --footer:#1c1d22;
  --footer-text:#e6e6e6;
  --white:#ffffff;
}
*{box-sizing:border-box;margin:0;padding:0}
html,body{width:1200px;height:4263px;overflow:hidden}
body{font-family:"Raleway",sans-serif;color:var(--ink);background:var(--white);position:relative}
.abs{position:absolute}
.serif{font-family:"Playfair Display",serif}
.btn{position:absolute;background:var(--red);color:var(--white);font-size:15px;font-weight:500;display:flex;align-items:center;justify-content:center;letter-spacing:.3px}

/* header */
.site-header{position:absolute;left:0;top:0;width:1200px;height:103px;background:var(--white)}
.brand{position:absolute;left:110px;top:20px;display:flex;align-items:center;gap:10px}
.brand-mark{width:26px;height:26px;border-radius:50%;background:var(--red)}
.brand-name{font-size:22px;font-weight:700;color:var(--red);letter-spacing:.5px}
.call-now{position:absolute;right:112px;top:18px;font-family:"Playfair Display",serif;font-size:14px;color:#555;display:flex;gap:8px;align-items:center}
.main-nav{position:absolute;right:112px;top:62px;display:flex;gap:28px;font-size:15px;color:#333}
.main-nav .active{color:var(--red)}

/* hero */
.hero{position:absolute;left:0;top:103px;width:1200px;height:582px}
.hero-photo{position:absolute;inset:0;background:linear-gradient(120deg,#6a6f78 0%,#3a4150 35%,#7a828c 60%,#c9cdd2 100%)}
.hero-shade{position:absolute;inset:0;background:rgba(20,22,28,.35)}
.hero-curve{position:absolute;left:0;bottom:0}
.hero h1{position:absolute;top:202px;width:100%;text-align:center;color:var(--white);font-family:"Playfair Display",serif;font-size:33px;font-weight:700}
.hero p{position:absolute;top:252px;width:100%;text-align:center;color:var(--white);font-size:15px;line-height:29px}
.dots{position:absolute;top:527px;left:550px;display:flex;gap:22px;align-items:center}
.dots span{width:7px;height:7px;border-radius:50%;background:var(--white)}
.dots span.on{width:14px;height:14px;border:2px solid var(--white);background:transparent;position:relative}
.dots span.on::after{content:"";position:absolute;left:3px;top:3px;width:4px;height:4px;border-radius:50%;background:var(--white)}

/* about */
.about-accent{left:372px;top:790px;width:218px;height:155px;background:var(--red)}
.about-photo{left:110px;top:808px;width:452px;height:358px;background:linear-gradient(135deg,#2d3440,#8b929b 45%,#d9dcdf 70%,#5b6270);box-shadow:0 0 0 1px #ddd}
.about h2{left:617px;top:828px;font-size:42px;font-weight:700}
.about p{left:617px;top:890px;width:464px;font-size:13.5px;line-height:31px;color:var(--muted);text-align:justify}

/* services */
.services-band{left:0;top:1270px;width:1200px;height:735px;background:var(--soft)}
.services-title{left:0;top:1300px;width:1200px;text-align:center;font-size:42px;font-weight:700}
.view-all{left:988px;top:1318px;font-size:15px;color:var(--red);text-decoration:underline;display:flex;align-items:center;gap:10px;font-weight:500}
.card{position:absolute;width:319px;height:421px;background:var(--white);box-shadow:0 0 0 1px #e6e6e6}
.card-photo{position:absolute;left:0;top:0;width:100%;height:257px}
.card-icon{position:absolute;left:123px;top:220px;width:74px;height:74px;border-radius:50%;background:var(--red);border:4px solid var(--white);display:flex;align-items:center;justify-content:center}
.card h3{position:absolute;top:305px;width:100%;text-align:center;font-size:14.5px;font-weight:600;letter-spacing:.3px}
.card p{position:absolute;top:330px;left:8px;right:8px;text-align:center;font-size:15px;line-height:27px;color:var(--muted)}

/* keep an eye */
.eye-kicker{left:0;top:2332px;width:1200px;text-align:center;color:var(--red);font-size:34px;font-weight:700}
.eye-title{left:0;top:2380px;width:1200px;text-align:center;font-size:34px;font-weight:700}
.eye-text{left:120px;top:2442px;width:960px;text-align:center;font-size:15px;line-height:32px;color:var(--muted)}

/* reviews */
.reviews{left:0;top:2705px;width:1200px;height:514px;background:var(--red)}
.reviews h2{position:absolute;left:110px;top:70px;color:var(--white);font-size:46px;font-weight:700}
.quote{position:absolute;left:120px;top:160px;width:464px;color:var(--white);font-style:italic;font-size:15.5px;line-height:35px;text-align:justify}
.qmark{font-family:"Playfair Display",serif;font-size:30px;font-style:normal;font-weight:700;line-height:0}
.reviewer{position:absolute;left:113px;top:385px;color:var(--white);font-style:italic;font-size:15px}
.reviewer-role{position:absolute;left:122px;top:410px;color:var(--white);font-size:13px}
.review-photo{position:absolute;left:621px;top:51px;width:468px;height:412px;background:linear-gradient(160deg,#c6c9cc,#8f9499 40%,#e9eaec 70%,#b8a89c)}

/* quote form */
.quote-title{left:110px;top:3333px;font-size:36px;line-height:45px;color:#333;font-weight:400;letter-spacing:.5px}
.quote-text{left:110px;top:3482px;width:448px;font-size:13.5px;line-height:27.5px;color:var(--muted);text-align:justify}
.quote-call{left:110px;top:3605px;font-family:"Playfair Display",serif;font-size:15px;color:var(--red)}
.quote-call span{text-decoration:underline}
.field{position:absolute;border:1px solid var(--line);background:var(--white);font-size:15px;color:#888;padding:17px 12px}

/* footer */
.site-footer{left:0;top:3778px;width:1200px;height:485px;background:var(--footer);color:var(--footer-text)}
.site-footer h4{position:absolute;top:70px;font-family:"Playfair Display",serif;font-weight:400;font-size:15px;letter-spacing:.5px}
.links{position:absolute;top:113px;list-style:none;font-size:15px;line-height:34px}
.contact-item{position:absolute;display:flex;align-items:center;gap:18px;font-size:15px;line-height:25px}
.ring{width:38px;height:38px;border-radius:50%;border:1.5px solid var(--footer-text);display:flex;align-items:center;justify-content:center;flex:none}
.social{position:absolute;left:946px;display:flex;align-items:center;gap:8px;font-size:15px}
.social .dot{width:32px;height:32px;border-radius:50%;border:1.5px solid var(--footer-text)}
.foot-row{position:absolute;top:368px;font-size:15px}
.foot-rule{position:absolute;left:110px;top:405px;width:980px;height:1px;background:#3a3b41}
.copyright{position:absolute;top:443px;width:100%;text-align:center;font-size:15px}
</style>
</head>
<body>

<header class="site-header">
  <div class="brand"><span class="brand-mark"></span><span class="brand-name">BRIGHTGATE</span></div>
  <div class="call-now">
    <svg width="14" height="14" viewBox="0 0 24 24" fill="none" stroke="#555" stroke-width="2"><path d="M5 3h4l2 5-2.5 1.5a11 11 0 0 0 6 6L16 13l5 2v4a2 2 0 0 1-2 2A16 16 0 0 1 3 5a2 2 0 0 1 2-2z"/></svg>
    CALL NOW - 832-555-0147
  </div>
  <nav class="main-nav">
    <span class="active">HOME</span><span>ABOUT</span><span>SERVICES</span><span>SOLUTIONS</span><span>SUPPORT</span><span>GALLERY</span><span>CONTACT US</span>
  </nav>
</header>

<section class="hero">
  <div class="hero-photo" role="img" aria-label="Technician in a hard hat installing a ceiling security camera"></div>
  <div class="hero-shade"></div>
  <h1>A GREAT PLACE FOR YOUR SECURITY NEEDS</h1>
  <p>Lorem ipsum dolor sit amet, consectetur adipiscing elit, sed do eiusmod tempor<br>incididunt ut labore et dolore magna aliqua</p>
  <div class="btn" style="left:523px;top:326px;width:154px;height:50px">GET STARTED</div>
  <div class="dots"><span class="on"></span><span></span><span></span><span></span></div>
  <svg class="hero-curve" width="1200" height="30" viewBox="0 0 1200 30" preserveAspectRatio="none"><path d="M0 0 Q600 40 1200 0 L1200 30 L0 30 Z" fill="#fff"/></svg>
</section>

<section class="about">
  <div class="abs about-accent"></div>
  <div class="abs about-photo" role="img" aria-label="Wall-mounted security camera on a building corner"></div>
  <h2 class="abs serif">ABOUT US</h2>
  <p class="abs">Nemo enim ipsam voluptatem quia voluptas sit aspernatur aut odit aut fugit, sed quia consequuntur magni dolores eos qui ratione voluptatem sequi nesciunt. Neque porro quisquam est, qui dolorem ipsum quia dolor sit amet, consectetur, adipisci velit, sed quia non numquam eius modi tempora incidunt ut labore et dolore magnam aliquam quaerat voluptatem.</p>
  <div class="btn" style="left:615px;top:1083px;width:155px;height:50px">READ MORE</div>
</section>

<section class="services">
  <div class="abs services-band"></div>
  <h2 class="abs serif services-title">OUR SERVICES</h2>
  <div class="abs view-all">VIEW ALL
    <svg width="16" height="12" viewBox="0 0 16 12" fill="none" stroke="#e8202a" stroke-width="1.6"><path d="M0 6h14M9 1l5 5-5 5"/></svg>
  </div>

  <article class="card" style="left:110px;top:1387px">
    <div class="card-photo" role="img" aria-label="Hand holding a phone beside a home monitoring camera" style="background:linear-gradient(135deg,#3f4550,#9aa0a8 55%,#eef0f2)"></div>
    <div class="card-icon"><svg width="34" height="34" viewBox="0 0 24 24" fill="none" stroke="#fff" stroke-width="1.5"><path d="M6 17V11a6 6 0 0 1 12 0v6M4 17h16M10 20h4"/></svg></div>
    <h3>ALARM MONITORING</h3>
    <p>Nemo enim ipsam voluptatem quia voluptas sit aspernatur aut odit aut fugit,</p>
  </article>
  <article class="card" style="left:441px;top:1387px">
    <div class="card-photo" role="img" aria-label="Dome camera above a crowded restaurant" style="background:linear-gradient(180deg,#d9d9d9,#b08462 55%,#6b4a36)"></div>
    <div class="card-icon"><svg width="34" height="34" viewBox="0 0 24 24" fill="none" stroke="#fff" stroke-width="1.5"><path d="M3 8l14 5-2 4-13-5zM17 13l3-1M7 14l-1 6M3 20h6"/></svg></div>
    <h3>SECURITY CAMERAS</h3>
    <p>Nemo enim ipsam voluptatem quia voluptas sit aspernatur aut odit aut fugit,</p>
  </article>
  <article class="card" style="left:771px;top:1387px">
    <div class="card-photo" role="img" aria-label="Finger pressing an access control keypad" style="background:linear-gradient(120deg,#5a5f66,#a9adb1 50%,#e0e2e4)"></div>
    <div class="card-icon"><svg width="34" height="34" viewBox="0 0 24 24" fill="none" stroke="#fff" stroke-width="1.5"><rect x="4" y="3" width="6" height="6"/><rect x="14" y="3" width="6" height="6"/><rect x="9" y="15" width="6" height="6"/><path d="M7 9v3h10V9M12 12v3"/></svg></div>
    <h3>ACCESS CONTROL</h3>
    <p>Nemo enim ipsam voluptatem quia voluptas sit aspernatur aut odit aut fugit,</p>
  </article>

  <article class="card" style="left:110px;top:1822px">
    <div class="card-photo" role="img" aria-label="Driver pressing a gate remote in front of a garage door" style="background:linear-gradient(180deg,#6b6e73,#9a9ca0 60%,#2a2b2e)"></div>
    <div class="card-icon"><svg width="34" height="34" viewBox="0 0 24 24" fill="none" stroke="#fff" stroke-width="1.5"><path d="M3 6v14M3 8h18v6H3M7 8v6M11 8v6M15 8v6"/></svg></div>
    <h3>GATE OPENERS</h3>
    <p>Nemo enim ipsam voluptatem quia voluptas sit aspernatur aut odit aut fugit,</p>
  </article>
  <article class="card" style="left:441px;top:1822px">
    <div class="card-photo" role="img" aria-label="Installer mounting a small camera on a wall" style="background:linear-gradient(120deg,#cfd0d2,#a7a9ac 55%,#c43a3a)"></div>
    <div class="card-icon"><svg width="34" height="34" viewBox="0 0 24 24" fill="none" stroke="#fff" stroke-width="1.5"><path d="M3 8l14 5-2 4-13-5zM17 13l3-1M7 14l-1 6M3 20h6"/></svg></div>
    <h3>COVERT CAMERA INSTALLATIONS</h3>
    <p>Nemo enim ipsam voluptatem quia voluptas sit aspernatur aut odit aut fugit,</p>
  </article>
  <article class="card" style="left:771px;top:1822px">
    <div class="card-photo" role="img" aria-label="Modern living room with a home theater screen" style="background:linear-gradient(180deg,#3b3631,#8a7a66 55%,#c9b89e)"></div>
    <div class="card-icon"><svg width="34" height="34" viewBox="0 0 24 24" fill="none" stroke="#fff" stroke-width="1.5"><rect x="5" y="3" width="14" height="9"/><path d="M3 14h18v5H3zM7 19v2M17 19v2"/></svg></div>
    <h3>HOME THEATER SYSTEMS</h3>
    <p>Nemo enim ipsam voluptatem quia voluptas sit aspernatur aut odit aut fugit,</p>
  </article>
</section>

<section class="eye">
  <h2 class="abs serif eye-kicker">KEEP AN EYE</h2>
  <h2 class="abs serif eye-title">ON YOUR LIFE QUALITY INSTALLATION SERVICE</h2>
  <p class="abs eye-text">Nemo enim ipsam voluptatem quia voluptas sit aspernatur aut odit aut fugit, sed quia consequuntur magni dolores eos qui ratione voluptatem sequi nesciunt. Neque porro quisquam est, qui dolorem ipsum quia dolor sit amet, consectetur, adipisci velit, sed quia non numquam eius modi tempora incidunt ut labore et dolore magnam aliquam quaerat voluptatem</p>
  <div class="btn" style="left:523px;top:2550px;width:154px;height:50px">CONTACT US</div>
</section>

<section class="abs reviews">
  <h2 class="serif">CUSTOMER REVIEWS</h2>
  <p class="quote"><span class="qmark" style="margin-left:-20px">&ldquo;</span> Nemo enim ipsam voluptatem quia voluptas sit aspernatur aut odit aut fugit, sed quia consequuntur magni dolores eos qui ratione voluptatem sequi nesciunt. Neque porro quisquam est, qui dolorem ipsum quia dolor sit amet, consectetur, adipisci velit, sed quia non numquam eius modi tempora incidunt ut labore et dolore magnam aliquam quaerat voluptatem <span class="qmark">&rdquo;</span></p>
  <div class="reviewer">- DANIEL HARTWELL</div>
  <div class="reviewer-role">Lorem ipsum dolor sit</div>
  <div class="review-photo" role="img" aria-label="Smiling client standing with arms crossed in an office"></div>
</section>

<section class="free-quote">
  <h2 class="abs serif quote-title">GET A FREE QUOTE AND<br>BRIGHTGATE AUDIO VIDEO<br>SECURITY OFFERS</h2>
  <p class="abs quote-text">Nemo enim ipsam voluptatem quia voluptas sit aspernatur aut odit aut fugit, sed quia consequuntur magni dolores eos qui ratione voluptatem sequi nesciunt. Neque porro quisquam est, qui dolorem ipsum quia dolor sit amet, consectetur, adipisci velit.</p>
  <div class="abs quote-call">Call Now - <span>832-555-0147</span></div>
  <div class="field" style="left:598px;top:3322px;width:488px;height:51px">Name</div>
  <div class="field" style="left:598px;top:3386px;width:488px;height:51px">Email</div>
  <div class="field" style="left:598px;top:3452px;width:236px;height:51px">Phone</div>
  <div class="field" style="left:849px;top:3452px;width:237px;height:51px">Zip</div>
  <div class="field" style="left:598px;top:3516px;width:488px;height:96px">Message</div>
  <div class="btn" style="left:851px;top:3625px;width:234px;height:51px">GET A FREE QUOTE</div>
</section>

<footer class="abs site-footer">
  <h4 style="left:112px">QUICK LINKS</h4>
  <ul class="links" style="left:113px"><li>Home</li><li>About</li><li>Services</li><li>Solutions</li><li>Support</li><li>Gallery</li><li>Contact Us</li></ul>
  <h4 style="left:327px">ABOUT</h4>
  <ul class="links" style="left:327px"><li>Team</li><li>News</li><li>Terms &amp; Condition</li><li>Privacy/Policy</li></ul>
  <h4 style="left:554px">CONTACT US</h4>
  <div class="contact-item" style="left:554px;top:113px">
    <span class="ring"><svg width="18" height="18" viewBox="0 0 24 24" fill="none" stroke="#e6e6e6" stroke-width="1.8"><path d="M12 22s7-7 7-12a7 7 0 0 0-14 0c0 5 7 12 7 12z"/><circle cx="12" cy="10" r="2.5"/></svg></span>
    <span>P.O. Box 419 Larkfield,<br>TX 77519</span>
  </div>
  <div class="contact-item" style="left:554px;top:203px">
    <span class="ring"><svg width="18" height="18" viewBox="0 0 24 24" fill="none" stroke="#e6e6e6" stroke-width="1.8"><path d="M5 3h4l2 5-2.5 1.5a11 11 0 0 0 6 6L16 13l5 2v4a2 2 0 0 1-2 2A16 16 0 0 1 3 5a2 2 0 0 1 2-2z"/></svg></span>
    <span>832-555-0147</span>
  </div>
  <div class="contact-item" style="left:554px;top:279px">
    <span class="ring"><svg width="18" height="18" viewBox="0 0 24 24" fill="none" stroke="#e6e6e6" stroke-width="1.8"><rect x="3" y="6" width="18" height="12"/><path d="M3 6l9 7 9-7"/></svg></span>
    <span>info.Brightgatesys@kelvamail.com</span>
  </div>
  <h4 style="left:946px">CONNECT WITH US</h4>
  <div class="social" style="top:115px"><span class="dot"></span>Friendboard</div>
  <div class="social" style="top:167px"><span class="dot"></span>Snapreel</div>
  <div class="social" style="top:219px"><span class="dot"></span>Chirpline</div>
  <div class="social" style="top:271px"><span class="dot"></span>Workgrid</div>
  <div class="foot-row" style="left:110px">Company license - #K41862509</div>
  <div class="foot-row" style="left:498px;display:flex;align-items:center;gap:8px">
    <svg width="16" height="16" viewBox="0 0 24 24" fill="none" stroke="#e6e6e6" stroke-width="1.8"><circle cx="12" cy="12" r="9"/><path d="M12 7v5l3 2"/></svg>Monday-Friday 8am-5pm
  </div>
  <div class="foot-row" style="right:112px">Fire license - # MTQ-6071852</div>
  <div class="foot-rule"></div>
  <div class="copyright">&copy; 2020 All Rights Reserved</div>
</footer>

</body>
</html>
```